Professional Photography Business cards

I need business cards that include my logo which I have uploaded. I run a photography business. I am open to ideas but I would like one side to have my logo and the other side to have my contact info. I don't have a website made but I do own a website domain. I have uploaded 2 different logo color schemes. My business colors are Blue, black , and white.

Business Name
Business Phone Number
Business Email
Business Website address
Instagram

Industry/Entity Type

Professional Photography

Contact Information for Business Card

Phone Number: 916-384-7702 email: info@tlane-studio.example Instagram: @t.lanestudio website doman- www.tlane-studio.example

Requirements
Must have
• I like the idea of a business card with a full black background front and back of card. My colors must include royal blue, black, and white

```html
<!DOCTYPE html>
<html lang="en">
<head>
<meta charset="utf-8">
<title>T. Lane Studio — Business Cards</title>
<link rel="stylesheet" href="https://fonts.googleapis.com/css2?family=Open+Sans:wght@400;600&display=swap">
<style>
  :root {
    --stage: #2b2b2d;
    --card: #141414;
    --royal-blue: #2e38b0;
    --white: #ffffff;
    --muted: #d9d9d9;
  }
  * { box-sizing: border-box; margin: 0; padding: 0; }
  html, body {
    width: 1200px; height: 900px; overflow: hidden;
    background: var(--stage);
    font-family: "Open Sans", Arial, sans-serif;
  }
  .stage {
    width: 1200px; height: 900px;
    display: flex; flex-direction: column; align-items: center; justify-content: center;
    gap: 40px;
  }
  .card {
    width: 700px; height: 400px;
    background: var(--card);
    border-radius: 24px;
    position: relative;
    box-shadow: 0 10px 30px rgba(0,0,0,0.45);
  }
  .brand {
    position: absolute;
    display: flex; align-items: center; gap: 22px;
  }
  .brand-name {
    color: var(--royal-blue);
    font-weight: 400;
    white-space: nowrap;
    letter-spacing: 0.02em;
  }
  .brand-mark {
    border: 5px solid var(--white);
    border-radius: 50%;
    flex: none;
  }
  .card-front .brand { left: 50%; top: 50%; transform: translate(-50%, -50%); }
  .card-front .brand-name { font-size: 48px; }
  .card-front .brand-mark { width: 110px; height: 110px; }

  .card-back .brand { left: 50%; top: 60px; transform: translateX(-50%); gap: 14px; }
  .card-back .brand-name { font-size: 30px; }
  .card-back .brand-mark { width: 66px; height: 66px; border-width: 4px; }

  .contact-list {
    position: absolute; left: 200px; bottom: 50px;
    list-style: none;
    display: flex; flex-direction: column; gap: 6px;
  }
  .contact-item {
    display: flex; align-items: center; gap: 10px;
    color: var(--white); font-size: 19px; letter-spacing: 0.01em;
  }
  .contact-icon { width: 16px; height: 16px; flex: none; }
  .contact-icon .stroke { fill: none; stroke: var(--royal-blue); stroke-width: 2; }
  .contact-icon .fill { fill: var(--royal-blue); }
</style>
</head>
<body>
<main class="stage">
  <section class="card card-front" aria-label="Card front">
    <div class="brand">
      <span class="brand-name">T. Lane Studio</span>
      <span class="brand-mark"></span>
    </div>
  </section>

  <section class="card card-back" aria-label="Card back">
    <div class="brand">
      <span class="brand-name">T. Lane Studio</span>
      <span class="brand-mark"></span>
    </div>
    <ul class="contact-list">
      <li class="contact-item">
        <svg class="contact-icon" viewBox="0 0 16 16" aria-hidden="true">
          <path class="fill" d="M3.5 1.5l2.5 0 1 3.5-1.8 1.2a8 8 0 0 0 4.6 4.6L11 9l3.5 1v2.5a2 2 0 0 1-2 2A11 11 0 0 1 1.5 3.5a2 2 0 0 1 2-2z"/>
        </svg>
        916-384-7702
      </li>
      <li class="contact-item">
        <svg class="contact-icon" viewBox="0 0 16 16" aria-hidden="true">
          <rect class="fill" x="1" y="3" width="14" height="10" rx="1"/>
          <path d="M1.5 3.8L8 9l6.5-5.2" fill="none" stroke="#141414" stroke-width="1.4"/>
        </svg>
        info@tlane-studio.example
      </li>
      <li class="contact-item">
        <svg class="contact-icon" viewBox="0 0 16 16" aria-hidden="true">
          <circle class="stroke" cx="8" cy="8" r="6.5"/>
          <path class="stroke" d="M1.5 8h13M8 1.5c-3 3.5-3 9.5 0 13M8 1.5c3 3.5 3 9.5 0 13" stroke-width="1.4"/>
        </svg>
        www.tlane-studio.example
      </li>
      <li class="contact-item">
        <svg class="contact-icon" viewBox="0 0 16 16" aria-hidden="true">
          <circle class="stroke" cx="8" cy="8" r="6.5"/>
        </svg>
        @t.lanestudio
      </li>
    </ul>
  </section>
</main>
</body>
</html>
```